Website Design for a holiday home letting busines

We require a redesign of our present website www.pinebrookstays.com. We want the website to stand out and look professional and clean to make holiday hunters want to book a caravan or lodge holiday with us. Our logo is red however we DO NOT want the website to be red. We want a natural colour scheme.

The final design should communicate that we are a professional company to book with.

On the home page we require;
Overview of company
Photo
Search box for holiday (check in)
Late Deals
Reviews
News

We would like the following pages designed; home page, available dates page, caravans page, content page.

The website should be responsive for smart phones. One website I do like is http://www.verdoliso.be/nl/

Target Market(s)

Families

Industry/Entity Type

Travel

Number of Pages Required

5+ page

Font styles to use
Serif

Requirements
Must have
• The project must be responsive for mobile phones and tablets.
• Ability to search for holiday home holidays
• We want a natural colour scheme.
Nice to have
• A style we like is http://www.verdoliso.be/nl/
Should not have
• Do not use red as a colour for the website. Our logo is red so this is the only time we want this used.

```html
<!DOCTYPE html>
<html lang="en">
<head>
<meta charset="utf-8">
<title>Pinebrook Stays – Private Holiday Rentals</title>
<link href="https://fonts.googleapis.com/css2?family=Lora:ital,wght@0,400;0,600;0,700;1,400&display=swap" rel="stylesheet">
<style>
:root{
  --brand:#c8312f;
  --accent:#4f6f3e;
  --accent-dark:#3b5430;
  --accent-soft:#cfe0b8;
  --wood:#8a6a48;
  --ink:#2f2f2a;
  --muted:#8a877f;
  --line:#e2ded6;
  --footer:#2e302a;
  --footer-text:#bdbab0;
  --white:#fff;
}
*{box-sizing:border-box;margin:0;padding:0}
html,body{width:1200px;height:2792px;overflow:hidden}
body{font-family:"Lora",Georgia,serif;color:var(--ink);background:var(--white);position:relative;font-size:13px}
.wrap{width:960px;margin:0 auto;position:relative}

/* hero */
.hero{position:absolute;top:0;left:0;width:1200px;height:760px;
  background:linear-gradient(180deg,#3b3556 0%,#7a5c86 28%,#c98a9a 42%,#3f6f8e 55%,#2a8fa8 72%,#56b9c6 100%)}
.hero-shade{position:absolute;inset:0;background:linear-gradient(90deg,rgba(0,0,0,0) 55%,rgba(0,0,0,.35) 100%)}
.topbar{position:absolute;top:0;left:0;width:1200px;height:110px;background:rgba(20,20,30,.55)}
.brand{position:absolute;left:120px;top:30px;display:flex;align-items:center;gap:12px}
.brand-mark{width:46px;height:46px;background:var(--brand);border-radius:6px}
.brand-name{color:var(--white);font-size:25px;font-weight:600}
.contact{position:absolute;right:120px;top:42px;display:flex;gap:28px;color:var(--white);font-size:14px}
.contact span{display:flex;align-items:center;gap:8px}
.contact svg{width:22px;height:22px}
.nav{position:absolute;top:110px;left:0;width:1200px;height:42px;background:rgba(10,10,20,.7)}
.nav ul{list-style:none;display:flex;gap:30px;padding-left:120px;height:42px;align-items:center}
.nav li{color:var(--white);font-size:13px;font-weight:600}
.nav li.active{color:var(--accent-soft)}
.hero-copy{position:absolute;left:790px;top:236px;width:290px;color:var(--white)}
.hero-copy h1{font-size:27px;font-weight:700;line-height:1.2}
.hero-copy p{font-size:13px;margin-top:8px;line-height:1.5}
.more{color:var(--accent-soft);font-weight:700;font-size:12px;margin-top:8px;display:block}
.booking{position:absolute;left:790px;top:430px;width:290px;color:var(--white)}
.booking h2{font-size:20px;font-weight:700;line-height:1.15}
.booking small{font-size:15px;font-weight:400}
.field{margin-top:14px;height:38px;background:var(--white);border-radius:3px;display:flex;align-items:center;justify-content:space-between;padding:0 12px;color:var(--muted);font-size:13px}
.btn{display:block;margin-top:14px;height:40px;background:var(--accent);color:var(--white);font-weight:700;font-size:14px;text-align:center;line-height:40px;border-radius:3px}

/* sections */
.section-title{text-align:center;font-size:29px;font-weight:600;color:var(--ink)}
.rooms{position:absolute;top:776px;left:0;width:1200px}
.arrows{position:absolute;right:0;top:6px;display:flex;gap:6px}
.arrows i{width:26px;height:26px;border-radius:50%;background:#ddd;display:block}
.arrows i + i{background:#bbb}
.view-all{text-align:center;color:var(--accent);font-size:13px;margin-top:6px}
.room-grid{display:flex;gap:15px;margin-top:44px}
.room{width:310px}
.room .photo{height:210px;background:linear-gradient(135deg,#c8b49a,#8f7560 60%,#5a4a3e)}
.room h3{text-align:center;font-size:17px;font-weight:600;margin:22px 0 14px}
.specs{display:flex;border:1px solid var(--line);height:38px;align-items:center;font-size:12px}
.specs span{flex:1;display:flex;align-items:center;gap:8px;padding:0 14px}
.specs span + span{border-left:1px solid var(--line)}
.specs b{margin-left:auto;font-weight:600}
.ico{width:14px;height:10px;background:var(--wood);border-radius:2px;display:inline-block}

.deals{position:absolute;top:1290px;left:0;width:1200px}
.deal-grid{display:flex;gap:11px;margin-top:44px}
.deal{width:232px}
.deal .photo{height:172px;background:linear-gradient(135deg,#d8c6a8,#9b7b5c 55%,#6a5444)}
.deal h4{font-size:11.5px;font-weight:700;margin:14px 0 8px;white-space:nowrap}
.deal h4 em{font-style:normal;font-weight:400;color:var(--muted)}
.deal h4 strong{color:var(--accent);font-weight:600}
.deal-foot{display:flex;gap:8px}
.deal-specs{flex:1;font-size:11px;border:1px solid var(--line)}
.deal-specs div{display:flex;align-items:center;gap:6px;height:20px;padding:0 8px}
.deal-specs div + div{border-top:1px solid var(--line)}
.deal-specs b{margin-left:auto}
.price{width:100px;background:#3d3f36;color:var(--white);font-weight:700;font-size:15px;display:flex;align-items:center;justify-content:center}

.reviews{position:absolute;top:1712px;left:0;width:1200px;height:428px;background:linear-gradient(180deg,#d7d2c6,#bfb8a8 50%,#d9d4c8)}
.review-grid{display:flex;gap:30px;padding-top:40px}
.review{width:300px;background:var(--white);height:296px;text-align:center;padding:18px 26px;box-shadow:0 2px 6px rgba(0,0,0,.08)}
.avatar{width:74px;height:74px;border-radius:50%;background:linear-gradient(135deg,#d9c2a6,#8f7560);margin:0 auto;border:3px solid #eee}
.review h5{color:var(--accent);font-size:17px;font-weight:600;margin-top:12px}
.review small{display:block;font-size:11px;color:var(--muted)}
.review p{font-style:italic;font-size:12px;line-height:1.6;color:#6f6c64;margin-top:14px}
.dots{display:flex;justify-content:center;gap:14px;margin-top:24px}
.dots i{width:8px;height:8px;border-radius:50%;background:#999;display:block}
.dots i.on{background:var(--accent)}

.news{position:absolute;top:2170px;left:0;width:1200px}
.news h2{font-size:26px;font-weight:600}
.news-grid{display:grid;grid-template-columns:330px 330px;gap:30px 40px;margin-top:30px}
.post h6{color:var(--accent);font-size:14px;font-weight:700}
.post p{font-size:12px;color:#666;margin-top:4px;line-height:1.5}
.post small{font-size:11px;color:var(--muted)}
.widget{position:absolute;right:0;top:10px;width:260px;height:240px;border:1px solid var(--line);padding:12px}
.widget-head{display:flex;align-items:center;gap:10px}
.widget-head i{width:34px;height:34px;background:var(--brand);border-radius:4px;display:block}
.widget-head b{font-size:14px}
.widget small{display:block;font-size:11px;color:var(--muted);margin:10px 0}
.faces{display:grid;grid-template-columns:repeat(4,50px);gap:8px}
.faces i{height:50px;background:linear-gradient(135deg,#cdb9a6,#8c7463);display:block}

.footer{position:absolute;top:2580px;left:0;width:1200px;height:180px;background:var(--footer);color:var(--footer-text)}
.footer .wrap{display:flex;padding-top:30px;gap:40px}
.newsletter{width:340px}
.newsletter h6{color:var(--white);font-size:13px;font-weight:700;letter-spacing:.5px}
.sub{display:flex;margin-top:12px}
.sub span{flex:1;height:32px;background:var(--white);font-size:12px;color:var(--muted);line-height:32px;padding-left:10px}
.sub b{width:40px;background:var(--accent);color:var(--white);text-align:center;line-height:32px}
.social{display:flex;gap:10px;margin-top:16px}
.social i{width:30px;height:30px;border-radius:50%;background:#55574e;display:block}
.links{list-style:none;font-size:12px;line-height:1.75;width:170px}
.bottom{position:absolute;top:2760px;left:0;width:1200px;height:32px;background:var(--accent-dark);color:var(--white);font-size:11px}
.bottom .wrap{line-height:32px}
</style>
</head>
<body>

<header class="hero" role="img" aria-label="Photo of overwater lodges lit at dusk above a turquoise lagoon">
  <div class="hero-shade"></div>
</header>

<div class="topbar">
  <div class="brand"><span class="brand-mark"></span><span class="brand-name">Pinebrook Stays</span></div>
  <div class="contact">
    <span><svg viewBox="0 0 22 22"><circle cx="11" cy="11" r="10" fill="none" stroke="#fff" stroke-width="1.5"/><path d="M8 6l2 3-1 1c1 2 2 3 4 4l1-1 3 2-1 2c-5 0-9-4-9-9z" fill="#fff"/></svg>01632 960 418</span>
    <span><svg viewBox="0 0 22 22"><circle cx="11" cy="11" r="10" fill="none" stroke="#fff" stroke-width="1.5"/><rect x="6" y="7.5" width="10" height="7" fill="none" stroke="#fff" stroke-width="1.3"/><path d="M6 7.5l5 4 5-4" fill="none" stroke="#fff" stroke-width="1.3"/></svg>info@pinebrookstays.com</span>
  </div>
</div>

<nav class="nav">
  <ul>
    <li class="active">Home</li><li>News</li><li>Reviews</li><li>Caravans &amp; Lodges</li>
    <li>2017 / 2018 Holidays</li><li>Payment Plans</li><li>Thornfield Bay</li><li>Contact Us</li>
  </ul>
</nav>

<div class="hero-copy">
  <h1>Private Holiday Rentals</h1>
  <p>Quality Lodges &amp; Caravans for rent at Thornfield Bay Holiday Park. Book online today.</p>
  <span class="more">READ MORE »</span>
</div>

<form class="booking">
  <h2>BOOK YOUR VACATION<br><small>in a minute</small></h2>
  <div class="field">Check in <svg width="16" height="16" viewBox="0 0 16 16"><rect x="1" y="3" width="14" height="12" fill="none" stroke="#999"/><path d="M1 6h14M4 1v3M12 1v3" stroke="#999"/></svg></div>
  <div class="field">Check Out <svg width="16" height="16" viewBox="0 0 16 16"><rect x="1" y="3" width="14" height="12" fill="none" stroke="#999"/><path d="M1 6h14M4 1v3M12 1v3" stroke="#999"/></svg></div>
  <span class="btn">BOOK NOW</span>
</form>

<section class="rooms">
  <div class="wrap">
    <h2 class="section-title">Our caravans and lodges</h2>
    <div class="arrows"><i></i><i></i></div>
    <p class="view-all">View all Rooms →</p>
    <div class="room-grid">
      <article class="room"><div class="photo" role="img" aria-label="Interior of a caravan lounge"></div><h3>The Hampton</h3>
        <div class="specs"><span><i class="ico"></i>Bedrooms<b>3</b></span><span><i class="ico"></i>Sleep<b>8</b></span></div></article>
      <article class="room"><div class="photo" role="img" aria-label="Interior of a lodge living room"></div><h3>The Westbury</h3>
        <div class="specs"><span><i class="ico"></i>Bedrooms<b>2</b></span><span><i class="ico"></i>Sleep<b>6</b></span></div></article>
      <article class="room"><div class="photo" role="img" aria-label="Interior of a caravan dining area"></div><h3>The Ashdale</h3>
        <div class="specs"><span><i class="ico"></i>Bedrooms<b>3</b></span><span><i class="ico"></i>Sleep<b>8</b></span></div></article>
    </div>
  </div>
</section>

<section class="deals">
  <div class="wrap">
    <h2 class="section-title">Late Deals</h2>
    <div class="deal-grid">
      <article class="deal"><div class="photo" role="img" aria-label="Caravan lounge interior"></div>
        <h4>The Seaview <em>Fri Aug 2016</em> <strong>(3 nights)</strong></h4>
        <div class="deal-foot"><div class="deal-specs"><div><i class="ico"></i>Bedrooms<b>3</b></div><div><i class="ico"></i>Sleep<b>8</b></div></div><div class="price">£149.00</div></div></article>
      <article class="deal"><div class="photo" role="img" aria-label="Caravan lounge interior"></div>
        <h4>The Ashdale <em>Fri Aug 2016</em> <strong>(3 nights)</strong></h4>
        <div class="deal-foot"><div class="deal-specs"><div><i class="ico"></i>Bedrooms<b>3</b></div><div><i class="ico"></i>Sleep<b>8</b></div></div><div class="price">£149.00</div></div></article>
      <article class="deal"><div class="photo" role="img" aria-label="Caravan lounge interior"></div>
        <h4>The Seaview <em>Fri Aug 2016</em> <strong>(3 nights)</strong></h4>
        <div class="deal-foot"><div class="deal-specs"><div><i class="ico"></i>Bedrooms<b>3</b></div><div><i class="ico"></i>Sleep<b>8</b></div></div><div class="price">£149.00</div></div></article>
      <article class="deal"><div class="photo" role="img" aria-label="Caravan lounge interior"></div>
        <h4>The Ashdale <em>Fri Aug 2016</em> <strong>(3 nights)</strong></h4>
        <div class="deal-foot"><div class="deal-specs"><div><i class="ico"></i>Bedrooms<b>3</b></div><div><i class="ico"></i>Sleep<b>8</b></div></div><div class="price">£149.00</div></div></article>
    </div>
  </div>
</section>

<section class="reviews" role="img" aria-label="Soft background photo of a caravan park">
  <div class="wrap">
    <div class="review-grid">
      <blockquote class="review"><div class="avatar" role="img" aria-label="Guest portrait"></div><h5>Claire Hadley</h5><small>The Hampton</small>
        <p>"Very clean on arrival. We could find everything we needed and the kids loved the park. Lovely stay, friendly owners and we will be booking again next year."</p></blockquote>
      <blockquote class="review"><div class="avatar" role="img" aria-label="Guest portrait"></div><h5>Megan Porter</h5><small>The Seaview</small>
        <p>"Had a great time and would definitely recommend these lodges. Everything was spotless and very comfortable accommodation."</p></blockquote>
      <blockquote class="review"><div class="avatar" role="img" aria-label="Guest portrait"></div><h5>Laura Benson</h5><small>The Ashdale</small>
        <p>"Absolutely delighted with the caravan we rented. Lovely welcome, clean and tidy throughout, a perfect family holiday."</p></blockquote>
    </div>
    <div class="dots"><i></i><i></i><i class="on"></i><i></i><i></i></div>
  </div>
</section>

<section class="news">
  <div class="wrap">
    <h2>Blog &amp; News</h2>
    <div class="news-grid">
      <div class="post"><h6>Fireworks Weekend</h6><p>Story goes here with fantastic views over lake</p><small>27 Sep 2016</small></div>
      <div class="post"><h6>Easter With Live Music</h6><p>Story goes here with fantastic views over lake</p><small>27 Sep 2016</small></div>
      <div class="post"><h6>Summer Show Live At Thornfield Bay</h6><p>Story goes here with fantastic views over lake</p><small>27 Sep 2016</small></div>
      <div class="post"><h6>Very clean on arrival</h6><p>Story goes here with fantastic views over lake</p><small>27 Sep 2016</small></div>
    </div>
    <aside class="widget">
      <div class="widget-head"><i></i><b>Pinebrook Stays</b></div>
      <small>1,248 people follow Pinebrook Stays</small>
      <div class="faces"><i></i><i></i><i></i><i></i><i></i><i></i><i></i><i></i></div>
    </aside>
  </div>
</section>

<footer class="footer">
  <div class="wrap">
    <div class="newsletter">
      <h6>JOIN OUR NEWSLETTER</h6>
      <div class="sub"><span>Enter your email</span><b>➜</b></div>
      <div class="social"><i></i><i></i><i></i><i></i></div>
    </div>
    <ul class="links"><li>About us</li><li>Deals</li><li>Caravans &amp; Lodges</li><li>2017 Holidays</li><li>2018 Holidays</li><li>Late Deals</li></ul>
    <ul class="links"><li>Thornfield Bay</li><li>Local Attractions</li><li>Seaside Walks</li><li>Contact Us</li><li>Reviews</li><li>Park Facilities</li></ul>
    <ul class="links"><li>Frequently Asked Questions</li><li>Park Entertainment Times</li><li>Privacy Policy</li><li>Booking Terms</li></ul>
  </div>
</footer>
<div class="bottom"><div class="wrap">Pinebrook Stays © 2016 All Rights Reserved. Terms of use and Privacy Policy</div></div>

</body>
</html>
```